Personalized Technology Company Needs a Business Card

I need a double-sided business card. Both sides will have the logo, and the contact information. One side will be black, with the white / gray logo, and the other will be white, with the black / gray logo. The black side will have the text "Custom Gaming PC's" and will have a water-cooled gaming PC image. The white side will have the text "Custom Business Computers & Consulting", and will have a business / enterprise PC image. Feel free to add a conservative image in the background, while the color remains unchanged. I'm uploading the base logo (transparent), so you can modify the colors, both the finished colored logos and an idea of ​​the business card (with the current information, just missing the website, which is www.velomindsystems.com, please add it.) Thank you so much for your effort, I'll be specting your cool designs. Good Luck!

Target Market(s)

Gamers & Entrepreneurs / Business Owners / Chief Technology Officers

Industry/Entity Type

Technology Equipment

Contact Information for Business Card

I need a double-sided business card. Both sides will have the logo, and the contact information. One side will be black, with the white/gray logo, and the other one will be white, with the black/gray logo. The black side will have the text "Custom Gaming PC's" and will have a water-cooled gaming PC image. The white side will have the text "Custom Business Computers & Consulting", and will have a business/enterprise PC image. Feel free to add a conservative image in the background, whilst the color remains unchanged.

I'm uploading the base logo (transparent), so you can modify the colors, both the finished colored logos and an idea of the business card (with the actual information, just missing the website, which is www.velomindsystems.com, please add it.)

Thank you so much for your effort, I'll be specting your cool designs. Good Luck!

Font styles to use
Serif

Colors
000000
757575
ffffff

Requirements
Must have
• Please See Description
Nice to have
• Please See Description
Should not have
• Please See Description

```html
<!DOCTYPE html>
<html lang="en">
<head>
<meta charset="utf-8">
<title>Velomind Systems – Business Card</title>
<link rel="stylesheet" href="https://fonts.googleapis.com/css2?family=Tinos:wght@400;700&display=swap">
<style>
  :root{
    --canvas:#2a2b2e;
    --black:#000000;
    --white:#ffffff;
    --gray:#757575;
    --light-gray:#bdbdbd;
    --accent:#2f8fe0;
    --photo-deep:#0b1a5c;
    --photo-mid:#1f4fd1;
    --photo-light:#7fd0ff;
  }
  *{box-sizing:border-box;margin:0;padding:0}
  html,body{width:1200px;height:800px;overflow:hidden}
  body{background:var(--canvas);font-family:"Tinos","Times New Roman",serif;position:relative}

  .card{position:absolute;top:246px;width:540px;height:308px;overflow:hidden;box-shadow:0 10px 30px rgba(0,0,0,.45)}
  .card--dark{left:40px;background:var(--black);color:var(--white)}
  .card--light{left:620px;background:var(--white);color:var(--black)}

  .photo{position:absolute}
  .photo--gaming{right:0;top:0;width:310px;height:250px;
    background:radial-gradient(circle at 60% 40%,var(--photo-light) 0%,var(--photo-mid) 35%,var(--photo-deep) 80%);
    clip-path:polygon(18% 0,100% 0,100% 100%,38% 100%,30% 82%,22% 76%,26% 60%,14% 48%,20% 30%,10% 16%)}
  .photo--server{left:0;bottom:0;width:300px;height:230px;
    background:radial-gradient(circle at 40% 55%,var(--photo-light) 0%,var(--photo-mid) 38%,var(--photo-deep) 85%);
    clip-path:polygon(0 0,62% 6%,70% 0,80% 20%,76% 36%,88% 48%,84% 70%,100% 86%,100% 100%,0 100%)}

  .tagline{position:absolute;background:var(--black);color:var(--white);font-size:13px;letter-spacing:.06em;text-transform:uppercase;border-radius:10px;padding:8px 18px;text-align:center;line-height:1.3;white-space:nowrap}
  .card--dark .tagline{right:20px;top:198px}
  .card--light .tagline{left:150px;bottom:26px}

  .brand{position:absolute;display:flex;align-items:center;gap:12px;white-space:nowrap}
  .brand__mark{width:34px;height:34px;flex:none}
  .brand__name{font-size:24px;letter-spacing:.12em;line-height:1}
  .card--dark .brand{left:36px;top:56px}
  .card--dark .brand__mark{background:var(--light-gray)}
  .card--dark .brand__name{color:var(--white)}
  .card--light .brand{right:28px;top:40px}
  .card--light .brand__mark{background:var(--gray)}
  .card--light .brand__name{color:var(--black)}

  .person{position:absolute;left:36px;top:134px}
  .person__name{font-size:17px;font-weight:700}
  .person__role{font-size:13px;color:var(--accent)}

  .contacts{position:absolute;left:36px;top:184px;font-size:12px;line-height:1.5}
  .contacts__row{display:flex;align-items:flex-start;gap:10px}
  .contacts__icon{width:14px;height:14px;margin-top:3px;flex:none}
  .contacts__rule{border-top:1px dotted var(--light-gray);width:230px;margin:8px 0 8px 24px}

  .chevron{position:absolute;left:14px;top:146px}

  .company{position:absolute;right:28px;top:128px;font-size:16px;color:var(--black)}
  .social{position:absolute;right:28px;top:172px;display:flex;gap:8px}
  .social__dot{width:16px;height:16px;border-radius:50%;background:var(--accent)}
  .website{position:absolute;right:28px;top:204px;font-size:12px;color:var(--gray)}
</style>
</head>
<body>

<section class="card card--dark" aria-label="Business card, black side">
  <div class="photo photo--gaming" role="img" aria-label="Photo of a water-cooled custom gaming PC with blue lighting"></div>
  <div class="tagline">Custom Gaming PC's</div>

  <div class="brand">
    <span class="brand__mark"></span>
    <span class="brand__name">VELOMIND SYSTEMS</span>
  </div>

  <svg class="chevron" width="14" height="22" viewBox="0 0 14 22"><path d="M12 2 L3 11 L12 20" fill="none" stroke="#2f8fe0" stroke-width="3"/></svg>

  <div class="person">
    <p class="person__name">Marco Ruiz Delano</p>
    <p class="person__role">(CEO &amp; Co-Founder)</p>
  </div>

  <div class="contacts">
    <div class="contacts__row">
      <svg class="contacts__icon" viewBox="0 0 14 14"><rect x="2" y="2" width="10" height="10" transform="rotate(45 7 7)" fill="#2f8fe0"/><path d="M5 4 q-1 3 4 6 l1-1.2 -1.5-1 -.8.6 q-1.5-1-2-2.4 l.7-.7 -.8-1.6z" fill="#000"/></svg>
      <div>+52 5510 - 2384<br>+52 55 - 4816 - 3057</div>
    </div>
    <div class="contacts__rule"></div>
    <div class="contacts__row">
      <svg class="contacts__icon" viewBox="0 0 14 14"><rect x="2" y="2" width="10" height="10" transform="rotate(45 7 7)" fill="#2f8fe0"/><rect x="4.5" y="5" width="5" height="4" fill="none" stroke="#000" stroke-width="1"/></svg>
      <div>contact@velomindsystems.com<br>www.velomindsystems.com</div>
    </div>
  </div>
</section>

<section class="card card--light" aria-label="Business card, white side">
  <div class="photo photo--server" role="img" aria-label="Photo of an enterprise server interface glowing in blue"></div>
  <div class="tagline">Custom Business<br>Computers &amp; Consulting</div>

  <div class="brand">
    <span class="brand__mark"></span>
    <span class="brand__name">VELOMIND SYSTEMS</span>
  </div>

  <p class="company">Velomind Systems PVT LTD</p>
  <div class="social" aria-label="Social media">
    <span class="social__dot"></span>
    <span class="social__dot"></span>
    <span class="social__dot"></span>
  </div>
  <p class="website">www.velomindsystems.com</p>
</section>

</body>
</html>
```